Poster of Core Values & Motto

Create our core values poster and motto. Attached are our core values and our Motto. This poster represents both of our companies Pindle Shred & KorvaBin.

Target Market(s)

Our team / employees

Industry/Entity Type

Shredding and Medical Waste

Colors
59FF00
82FF00
B8FF75
E3FFCB
F4FFEA
EB3D1F
EC4F4E
F09395
F8D3D4
FCEDEE

Requirements
Must have
• Include both companies logos

```html
<!DOCTYPE html>
<html lang="en">
<head>
<meta charset="utf-8">
<title>Core Values – KorvaBin &amp; Pindle Shred</title>
<link href="https://fonts.googleapis.com/css2?family=Barlow+Semi+Condensed:wght@500;700&family=Montserrat:wght@300;800&family=Nunito:wght@800&display=swap" rel="stylesheet">
<style>
  :root{
    --page:#e6e7e8;
    --white:#ffffff;
    --brand-red:#d7262e;
    --brand-green:#00a651;
    --band-green:#009b48;
    --swoosh-green:#1a9b46;
    --shadow:#9b9b9f;
    --synergy:#33a9ff;
    --excellence:#ff8c00;
    --efficient:#1b8e48;
    --efficient-icon:#33f08a;
    --secure:#41688b;
    --secure-icon:#80cfff;
    --honesty:#dc524f;
    --honesty-icon:#f6a19d;
    --dependable:#363a72;
    --dependable-icon:#6d79e0;
    --medal:#ffee00;
  }
  *{box-sizing:border-box;margin:0;padding:0}
  html,body{width:801px;height:1200px;overflow:hidden}
  body{background:var(--page);position:relative;font-family:"Nunito",sans-serif}

  .masthead{position:absolute;left:0;top:0;width:801px;height:185px;background:var(--white)}
  .brand{position:absolute;font-family:"Montserrat",sans-serif;font-weight:800;line-height:1}
  .brand--korvabin{left:67px;top:60px;font-size:46px;color:var(--brand-red);letter-spacing:1px}
  .brand--pindle{left:520px;top:46px;display:flex;align-items:center;gap:10px;color:var(--brand-green)}
  .brand--pindle .mark{width:56px;height:56px;border-radius:50%;background:var(--brand-green)}
  .brand--pindle .name{font-size:29px;line-height:1.02}

  .motto{position:absolute;left:0;width:801px;top:126px;text-align:center;font-family:"Barlow Semi Condensed",sans-serif;font-weight:500;font-size:29px;color:var(--brand-red);white-space:nowrap}
  .motto strong{font-weight:700;font-size:34px}
  .motto-swoosh{position:absolute;left:336px;top:160px}

  .values-band{position:absolute;left:0;top:185px;width:801px;height:121px;background:var(--band-green);display:flex;align-items:center;justify-content:center;color:var(--white);font-family:"Montserrat",sans-serif;font-size:60px;letter-spacing:1px}
  .values-band .light{font-weight:300;margin-right:18px}
  .values-band .bold{font-weight:800}

  .value{position:absolute;left:53px;width:695px;height:123px;display:flex;box-shadow:5px 4px 0 var(--shadow)}
  .value__label,.value__text{width:50%;height:100%;position:relative;display:flex;align-items:center}
  .value__text{background:var(--white);font-weight:800;font-size:19px;line-height:1.22;padding:0 34px 0 26px}
  .value--text-left .value__text{justify-content:flex-end;text-align:right}
  .value__label{color:var(--white);font-family:"Montserrat",sans-serif;font-weight:800;font-size:27px;line-height:.95}
  .value--label-left .value__label{justify-content:flex-end;padding-right:34px}
  .value--label-right .value__label{padding-left:28px}
  .icon{position:absolute}

  .v-synergy{top:332px}
  .v-synergy .value__label{background:var(--synergy)}
  .v-synergy .value__text{color:var(--synergy)}
  .v-synergy .icon{left:10px;top:8px;width:105px;height:110px;border-radius:50%;background:radial-gradient(circle,transparent 28%,#7ee7ff 30%,#6fe0f5 70%,transparent 72%)}

  .v-excellence{top:469px}
  .v-excellence .value__label{background:var(--excellence)}
  .v-excellence .value__text{color:var(--excellence)}
  .v-excellence .icon{right:24px;top:6px;width:84px;height:112px;background:linear-gradient(var(--medal),#ffd200);border-radius:42px 42px 6px 6px}

  .v-efficient{top:606px}
  .v-efficient .value__label{background:var(--efficient)}
  .v-efficient .value__text{color:var(--efficient)}
  .v-efficient .icon{left:22px;top:14px;width:96px;height:96px;border-radius:50%;background:linear-gradient(135deg,var(--efficient-icon),#27c874)}

  .v-secure{top:743px}
  .v-secure .value__label{background:var(--secure)}
  .v-secure .value__text{color:var(--secure)}
  .v-secure .icon{right:30px;top:12px;width:84px;height:98px;border-radius:14px 14px 42px 42px;background:linear-gradient(var(--secure-icon),#6cc0f5)}

  .v-honesty{top:880px;left:50px;width:698px}
  .v-honesty .value__label{background:var(--honesty);padding-right:32px}
  .v-honesty .value__text{color:var(--honesty)}
  .v-honesty .icon{left:10px;top:26px;width:134px;height:84px;border-radius:40px;background:linear-gradient(90deg,var(--honesty-icon),#f7b0ab)}

  .v-dependable{top:1017px}
  .v-dependable .value__text{color:var(--dependable)}
  .v-dependable .value__label{background:var(--dependable)}
  .v-dependable .icon{right:20px;top:16px;width:78px;height:96px;border-radius:39px 39px 10px 10px;background:linear-gradient(var(--dependable-icon),#5a66d6)}
</style>
</head>
<body>
  <header class="masthead">
    <div class="brand brand--korvabin">KorvaBin</div>
    <div class="brand brand--pindle">
      <span class="mark"></span>
      <span class="name">Pindle<br>Shred</span>
    </div>
    <p class="motto">REMIND PEOPLE WHAT <strong>GREAT SERVICE</strong> LOOKS LIKE!</p>
    <svg class="motto-swoosh" width="236" height="18" viewBox="0 0 236 18" aria-hidden="true">
      <path d="M3 15 Q110 0 232 6" fill="none" stroke="var(--swoosh-green)" stroke-width="5" stroke-linecap="round"/>
    </svg>
  </header>

  <section class="values-band">
    <span class="light">CORE</span><span class="bold">VALUES</span>
  </section>

  <article class="value value--label-left v-synergy">
    <div class="value__label">
      <div class="icon" role="img" aria-label="Circle of joined helping hands"></div>
      SYNERGY /<br>TEAMWORK
    </div>
    <div class="value__text">Get It Done Attitude<br>with Humble confidence</div>
  </article>

  <article class="value value--text-left value--label-right v-excellence">
    <div class="value__text">Exceed expectation<br>with a smile</div>
    <div class="value__label">
      EXCELLENCE
      <div class="icon" role="img" aria-label="Award rosette with star and ribbons"></div>
    </div>
  </article>

  <article class="value value--label-left v-efficient">
    <div class="value__label">
      <div class="icon" role="img" aria-label="Clock with circular arrow"></div>
      EFFICIENT
    </div>
    <div class="value__text">On-Time, sense of urgency,<br>always trying to improve</div>
  </article>

  <article class="value value--text-left value--label-right v-secure">
    <div class="value__text">We are just as secure as an<br>armored truck with money</div>
    <div class="value__label">
      SAFE &amp;<br>SECURE
      <div class="icon" role="img" aria-label="Shield with padlock"></div>
    </div>
  </article>

  <article class="value value--label-left v-honesty">
    <div class="value__label">
      <div class="icon" role="img" aria-label="Handshake"></div>
      HONESTY/<br>INTEGRITY
    </div>
    <div class="value__text">Do the right thing</div>
  </article>

  <article class="value value--text-left value--label-right v-dependable">
    <div class="value__text">Do what you say you will do</div>
    <div class="value__label">
      DEPENDABLE
      <div class="icon" role="img" aria-label="Person with magnifier giving a thumbs up"></div>
    </div>
  </article>
</body>
</html>
```